Awesome photographers card for an awesome new business

Double sided business card Black background and silver logo in middle on one side. Details on otherside. please keep it simple

Industry/Entity Type

Photographer

Contact Information for Business Card

Gerald Fenwick
0452817360
GeraldFenwickPhotography47@mailbox.test
www.GeraldFenwickPhotography.test.au
Instagram _Gerald_fenwick

Requirements
Must have
• My logo in Silver
• please use instagram logo instead of "Instagram"

```html
<!DOCTYPE html>
<html lang="en">
<head>
<meta charset="utf-8">
<title>Gerald Fenwick Photography – Business Card</title>
<link rel="stylesheet" href="https://fonts.googleapis.com/css2?family=Questrial&display=swap">
<style>
  :root {
    --backdrop: #bdbdbd;
    --card-light: #f4f4f4;
    --card-dark: #141414;
    --ink: #4a4a4a;
    --ink-name: #555555;
    --rule: #8a8a8a;
    --silver: #c9c9c9;
  }
  * { margin: 0; padding: 0; box-sizing: border-box; }
  html, body {
    width: 1200px;
    height: 960px;
    overflow: hidden;
    background: var(--backdrop);
    font-family: "Questrial", "Century Gothic", sans-serif;
  }
  .canvas {
    position: relative;
    width: 1200px;
    height: 960px;
  }
  .card {
    position: absolute;
    left: 321px;
    width: 600px;
    height: 342px;
    border-radius: 16px;
  }
  .card--details {
    top: 126px;
    background: var(--card-light);
  }
  .card--brand {
    top: 501px;
    background: var(--card-dark);
  }
  .details {
    position: absolute;
    right: 64px;
    top: 116px;
    text-align: right;
    color: var(--ink);
  }
  .details__name {
    font-size: 22px;
    font-weight: 400;
    letter-spacing: 0.3px;
    color: var(--ink-name);
    text-transform: uppercase;
    line-height: 28px;
    -webkit-text-stroke: 0.4px var(--ink-name);
  }
  .details__rule {
    width: 46px;
    height: 2px;
    background: var(--rule);
    margin: 6px 0 14px auto;
  }
  .details__list {
    list-style: none;
    font-size: 14px;
    line-height: 18px;
  }
  .brand-mark {
    position: absolute;
    left: 50%;
    top: 50%;
    transform: translate(-50%, -50%);
    width: 210px;
    height: 210px;
  }
  .brand-mark__ring {
    position: absolute;
    inset: 0;
    border: 3px solid var(--silver);
    border-radius: 50%;
  }
  .brand-mark__name {
    position: absolute;
    inset: 0;
    display: flex;
    flex-direction: column;
    align-items: center;
    justify-content: center;
    color: var(--silver);
    font-size: 18px;
    letter-spacing: 3px;
    line-height: 26px;
    text-transform: uppercase;
    text-align: center;
  }
</style>
</head>
<body>
  <main class="canvas">
    <section class="card card--details" aria-label="Contact side">
      <div class="details">
        <h1 class="details__name">Gerald Fenwick</h1>
        <div class="details__rule"></div>
        <ul class="details__list">
          <li>Phone 0452817360</li>
          <li>GeraldFenwickPhotography47@mailbox.test</li>
          <li>www.GeraldFenwickPhotography.test.au</li>
          <li>Instagram _Gerald_fenwick</li>
        </ul>
      </div>
    </section>

    <section class="card card--brand" aria-label="Brand side">
      <div class="brand-mark">
        <div class="brand-mark__ring"></div>
        <p class="brand-mark__name">Gerald<br>Fenwick<br>Photography</p>
      </div>
    </section>
  </main>
</body>
</html>
```